Business card for Crestline Bathrooms

Please design a business card for our bathroom renovation business. You can use my existing logo, but if you have an idea to modernize it, I would like to see it. Please see attached files first. I would like to use the blue and the orange theme. I like the concept of using the shower head in the logo. Please find following a design (or two) that I have been trying to create with my limited resources. That design was for a sign, but I was going to adopt it and use it as a business card as well. I like the concept of the water splash but I don’t think it “flows” nicely together with the logo. Another thought is that maybe creating the logo out of water splash could work and have a dramatic effect (like the water text and the butterfly picture attached with similar background instead of white). If the above doesn’t work I would like to see a modern simplified design. One of the attached files named as the unwanted business card has all the details that I want included in the business card. Please note that it is two sided.
Updates

I am very thankful for the designs that I have received, but they are very similar and only a couple of attempts to do something with the water splash as per my original brief. Modernizing the logo and having it made out of out of water splash with the orange as color accent could work and have a dramatic effect (like the water text and the butterfly picture attached with similar background instead of white). Please do not use the butterfly itself! This is just an example that images can be created out of water splash.

Contact Information for Business Card

all the details are on the unwonted business card file included

Colors
3176b5

Requirements
Nice to have
• Copied from the brief:
• ... maybe creating the logo out of water splash could work and have a dramatic effect (like the water text and the butterfly picture attached with similar background instead of white). Please do not use the butterfly itself!
Should not have
• I am getting designs with a butterfly. The butterfly picture was an example of creating something from a water splash. The butterfly itself has no association with anything other than the concept of creating a logo out of water splash. Sorry, I thought I was clear in the brief.

```html
<!DOCTYPE html>
<html lang="en">
<head>
<meta charset="utf-8">
<title>Crestline Bathrooms – Business Card</title>
<link rel="stylesheet" href="https://fonts.googleapis.com/css2?family=Roboto:wght@400;500&family=Fira+Sans:wght@300&family=Libre+Baskerville:wght@700&display=swap">
<style>
  :root {
    --navy: #0d416b;
    --salmon: #ee7d6b;
    --card: #f3f3f3;
    --backdrop: #e6e8eb;
    --white: #ffffff;
  }
  * { box-sizing: border-box; margin: 0; padding: 0; }
  html, body { width: 1200px; height: 960px; overflow: hidden; }
  body { background: var(--backdrop); position: relative; font-family: "Roboto", sans-serif; }

  .card {
    position: absolute;
    width: 600px;
    height: 343px;
    border-radius: 22px;
    background: var(--card);
    overflow: hidden;
    box-shadow: 0 2px 6px rgba(0,0,0,0.18);
  }
  .card--front { left: 315px; top: 113px; }
  .card--back { left: 311px; top: 472px; }

  .front-panel { position: absolute; inset: 0; width: 600px; height: 343px; }

  .shower-illustration {
    position: absolute;
    left: 390px; top: 6px;
    width: 200px; height: 210px;
    border-radius: 40px;
    background: radial-gradient(ellipse at 40% 35%, rgba(238,125,107,0.55), rgba(13,65,107,0.22) 60%, rgba(243,243,243,0) 75%);
  }

  .contact { position: absolute; left: 25px; color: var(--white); font-size: 14.5px; line-height: 19px; }
  .contact--address { top: 54px; }
  .contact--lines { top: 99px; }
  .contact-row { display: flex; align-items: center; gap: 9px; height: 19.5px; }
  .contact-row svg { width: 13px; height: 13px; fill: var(--white); flex: none; }

  .services {
    position: absolute; left: 21px; top: 180px;
    color: var(--white);
    font-family: "Fira Sans", sans-serif; font-weight: 300;
    font-size: 13.6px; line-height: 18.3px;
  }

  .badges { position: absolute; left: 22px; top: 274px; display: flex; align-items: center; }
  .badge-square { width: 32px; height: 34px; border-radius: 7px; background: var(--white); }
  .badge-divider { width: 1px; height: 34px; background: var(--white); margin: 0 17px; opacity: 0.9; }
  .badge-wide { width: 118px; height: 26px; border-radius: 3px; background: var(--white); }

  .holder-name {
    position: absolute; right: 32px; top: 251px;
    font-family: "Libre Baskerville", serif; font-weight: 700;
    font-size: 17.5px; color: var(--navy); letter-spacing: 0.2px;
  }

  .brand {
    position: absolute; left: 0; right: 0; top: 118px;
    display: flex; flex-direction: column; align-items: center;
  }
  .brand-mark { width: 34px; height: 34px; border-radius: 50%; background: var(--salmon); margin-bottom: 10px; }
  .brand-name {
    font-family: "Roboto", sans-serif; font-weight: 500;
    color: var(--navy); font-size: 40px; line-height: 44px; text-align: center;
  }
</style>
</head>
<body>

<section class="card card--front">
  <svg class="front-panel" viewBox="0 0 600 343" aria-hidden="true">
    <path fill="var(--navy)" d="M0,0 H405 C330,0 250,20 262,92 C272,150 338,188 332,248 C326,300 255,320 190,343 H0 Z"/>
  </svg>
  <div class="shower-illustration" role="img" aria-label="Shower head illustration spraying water"></div>

  <address class="contact contact--address" style="font-style:normal">
    PO Box 41<br>Larkfield 2840
  </address>

  <div class="contact contact--lines">
    <div class="contact-row">
      <svg viewBox="0 0 24 24"><path d="M6.6 10.8a15 15 0 0 0 6.6 6.6l2.2-2.2c.3-.3.7-.4 1-.2 1.1.4 2.3.6 3.6.6.6 0 1 .4 1 1V20c0 .6-.4 1-1 1A17 17 0 0 1 3 4c0-.6.4-1 1-1h3.5c.6 0 1 .4 1 1 0 1.3.2 2.5.6 3.6.1.3 0 .7-.2 1z"/></svg>
      <span>0400 555 218</span>
    </div>
    <div class="contact-row">
      <svg viewBox="0 0 24 24"><path d="M7 1h10a2 2 0 0 1 2 2v18a2 2 0 0 1-2 2H7a2 2 0 0 1-2-2V3a2 2 0 0 1 2-2zm0 3v14h10V4z"/></svg>
      <span>6200 4417</span>
    </div>
    <div class="contact-row">
      <svg viewBox="0 0 24 24"><path d="M2 5h20v14H2zm2 2v.5l8 5 8-5V7z"/></svg>
      <span>peter@crestlinebathrooms.com.au</span>
    </div>
  </div>

  <ul class="services" style="list-style:none">
    <li>Complete Bathroom Renovations &amp; Remodelling</li>
    <li>Highly Skilled &amp; Qualified Tradespeople</li>
    <li>Professional Service From Concept To Completion</li>
    <li>All Work Guaranteed</li>
  </ul>

  <div class="badges">
    <span class="badge-square" aria-hidden="true"></span>
    <span class="badge-divider" aria-hidden="true"></span>
    <span class="badge-wide" aria-hidden="true"></span>
  </div>

  <p class="holder-name">PETER HOLLANDS</p>
</section>

<section class="card card--back">
  <div class="brand">
    <span class="brand-mark" aria-hidden="true"></span>
    <p class="brand-name">Crestline<br>Bathrooms</p>
  </div>
</section>

</body>
</html>
```